International Medical Company Needs a Website Design for a Support Site

We need a website design for a support site we are doing for ostomates called Bright Returns. We are an international company but this website is for our Australian market.

The website is a support site for people who are living with an Ostomy or Bowel Disease. This is a site where they can read other ostomates' stories and how they are dealing with the fact that they have to wear a pouch everyday.

The URL for our US site is: http://www.brightreturnsite.example/

We need to use the same logo but we have freedom around the color scheme. We are not fond of the brown color scheme used in our US site and are happy for designs to be submitted with alternatives.

• We want the design to be clean, inspiring, modern and inviting.
• We would like to see a design for the mainpage / homepage and one of the subpages
• We only require the PSD / image files (no HTML needed)

Attached to this project is our sitemap, an example wireframe and the logos. We are happy for you to play around with different options and don't have to stick to the layout shown in the wireframe.

If you have any further questions please ask.

Industry/Entity Type

It Company

```html
<!DOCTYPE html>
<html lang="en">
<head>
<meta charset="utf-8">
<title>Bright Returns — Sharing stories and giving hope</title>
<link rel="stylesheet" href="https://fonts.googleapis.com/css2?family=Ubuntu:ital,wght@0,400;0,500;0,700;1,400&display=swap">
<style>
  :root {
    --green: #6fd651;
    --grey-bg: #e7e6ea;
    --grey-light: #efeef1;
    --grey-text: #5f5f63;
    --dark-band: #34444f;
    --white: #ffffff;
  }
  * { box-sizing: border-box; margin: 0; padding: 0; }
  html, body { width: 1200px; height: 789px; overflow: hidden; }
  body {
    position: relative;
    font-family: "Ubuntu", sans-serif;
    background: var(--grey-bg);
    color: var(--grey-text);
  }
  .header-sheen {
    position: absolute; inset: 0 0 auto 0; height: 572px;
    background: linear-gradient(120deg, #dedde2 0%, var(--grey-light) 45%, #e4e3e7 100%);
    clip-path: polygon(460px 0, 1200px 0, 1200px 572px, 0 572px, 0 0);
  }
  .brand-art {
    position: absolute; left: 31px; top: 37px; width: 236px; height: 202px;
    background: radial-gradient(ellipse at 45% 50%, #b9bcc0 0%, #d6d6da 55%, transparent 75%);
  }
  .brand {
    position: absolute; left: 172px; top: 29px;
    font-size: 19px; font-weight: 500; letter-spacing: 1.2px;
    color: var(--grey-text); text-decoration: none;
  }
  .share-link {
    position: absolute; left: 476px; top: 33px;
    font-size: 13px; font-weight: 500; color: var(--green); text-decoration: none;
  }
  .country-select {
    position: absolute; left: 806px; top: 28px; width: 116px; height: 28px;
    background: var(--white); border: 1px solid #cfcfd3;
    font-size: 12px; font-style: italic; color: #888;
    padding: 7px 0 0 13px;
  }
  .country-select::after {
    content: "▼"; position: absolute; right: 9px; top: 7px; font-size: 10px; font-style: normal; color: #666;
  }
  .search {
    position: absolute; left: 942px; top: 28px; width: 141px; height: 28px;
    background: var(--white); border: 1px solid #cfcfd3;
    font-size: 12px; font-style: italic; color: #888; padding: 6px 0 0 16px;
  }
  .search svg { position: absolute; right: 8px; top: 7px; }
  .main-nav {
    position: absolute; left: 319px; top: 75px; width: 881px; height: 70px;
    background: var(--green);
    clip-path: polygon(75px 0, 100% 0, 100% 100%, 0 100%);
  }
  .main-nav a {
    position: absolute; top: 28px; font-size: 13.5px; color: var(--white);
    text-decoration: none; letter-spacing: .2px;
  }
  .hero-photo {
    position: absolute; left: 0; top: 161px; width: 1083px; height: 409px;
    background: linear-gradient(100deg, #8e8b88 0%, #d9c2ba 30%, #e8ccc4 55%, #6f5b57 80%, #c9c6c4 100%);
    clip-path: polygon(281px 0, 1083px 0, 769px 409px, 0 409px, 0 401px);
  }
  .hero-copy {
    position: absolute; left: 863px; top: 397px; width: 221px; text-align: right; z-index: 2;
  }
  .hero-title { font-size: 16px; font-weight: 500; line-height: 18px; color: var(--grey-text); }
  .hero-title .accent { color: var(--green); }
  .hero-text { margin-top: 10px; font-size: 13px; line-height: 15.5px; color: #5a5a5e; }
  .hero-actions {
    position: absolute; left: 875px; top: 524px; width: 208px; height: 24px;
  }
  .btn {
    position: absolute; top: 0; height: 24px; background: var(--green); color: var(--white);
    font-size: 10px; font-weight: 500; line-height: 24px; text-align: center; text-decoration: none;
  }
  .btn-share { left: 0; width: 84px; }
  .btn-read { left: 123px; width: 85px; }
  .or { position: absolute; left: 98px; top: 2px; font-size: 14px; color: #555; }
  .intro {
    position: absolute; left: 0; top: 572px; width: 1200px; height: 217px;
    background: var(--dark-band); color: var(--white); text-align: center;
  }
  .intro h1 { margin-top: 42px; font-size: 27px; font-weight: 700; }
  .intro .rule { width: 38px; height: 1px; background: #aeb6bb; margin: 14px auto 18px; }
  .intro p { width: 900px; margin: 0 auto; font-size: 19.5px; line-height: 28px; color: #e9ecee; }
</style>
</head>
<body>
  <div class="header-sheen"></div>
  <div class="brand-art" role="img" aria-label="Bird formed from scattered grey and green leaves"></div>
  <a class="brand" href="http://www.brightreturnsite.example/">BRIGHTRETURNS</a>
  <a class="share-link" href="#">SHARE YOUR STORY</a>
  <div class="country-select">Select country</div>
  <div class="search">Search
    <svg width="12" height="12" viewBox="0 0 12 12" fill="none" stroke="#999" stroke-width="1.4"><circle cx="7" cy="5" r="3.6"/><path d="M4.4 7.6 1 11"/></svg>
  </div>

  <nav class="main-nav">
    <a href="#" style="left:133px">ABOUT US</a>
    <a href="#" style="left:228px">PERSONAL STORIES</a>
    <a href="#" style="left:380px">TIPS FOR LIVING</a>
    <a href="#" style="left:513px">NEWS</a>
    <a href="#" style="left:579px">RESOURCES</a>
    <a href="#" style="left:684px">CONTACT US</a>
  </nav>

  <div class="hero-photo" role="img" aria-label="Three friends laughing together on a sofa with coffee and snacks"></div>

  <div class="hero-copy">
    <div class="hero-title"><span class="accent">SHARING</span> STORIES<br>AND GIVING <span class="accent">HOPE</span></div>
    <p class="hero-text">to people around the world who<br>are facing inflammatory bowel<br>disease, colorectal cancer, or have<br>had ostomy surgery.</p>
  </div>
  <div class="hero-actions">
    <a class="btn btn-share" href="#">SHARE A STORY</a>
    <span class="or">or</span>
    <a class="btn btn-read" href="#">READ STORIES</a>
  </div>

  <section class="intro">
    <h1>Plan, make, achieve and enjoy your life!</h1>
    <div class="rule"></div>
    <p>Cum sociis natoque penatibus et magnis dis parturient montes, nascetur ridiculus mus. Sed posuere consectetur est at lobortis. Maecenas sed diam eget risus varius blandit sit amet non magna.</p>
  </section>
</body>
</html>
```